Spiritual Healing bussiness needs logo/business card

Simple, clean looking logo/card
For spiritual business with healing services and occult rituals

Contact Information for Business Card

Needs my name: Tobin Varley
Business name: Lantern Healing Shop
Services provided and worded in this way:

Reiki Healing
Tarot
Oils
Rituals Of Change

Can look occult like but with light energy.

Colors
0255a3
3276b5
85abd2
33a6d7
85cae6
0292cd

```html
<!DOCTYPE html>
<html lang="en">
<head>
<meta charset="utf-8">
<title>Lantern Healing Shop – Business Card</title>
<link href="https://fonts.googleapis.com/css2?family=Roboto:wght@700;900&family=Work+Sans:wght@400;500&display=swap" rel="stylesheet">
<style>
  :root {
    --stage: #161616;
    --card: #242424;
    --card-light: #2e2e2e;
    --brand-blue: #0255a3;
    --accent-blue: #3276b5;
    --text-light: #f2f2f2;
    --emboss: #5a5a5a;
  }
  * { margin: 0; padding: 0; box-sizing: border-box; }
  html, body { width: 1200px; height: 900px; overflow: hidden; }
  body {
    background: var(--stage);
    display: flex;
    flex-direction: column;
    align-items: center;
    justify-content: center;
    gap: 40px;
    font-family: "Work Sans", sans-serif;
  }
  .card {
    width: 630px;
    height: 360px;
    background: linear-gradient(135deg, var(--card) 0%, var(--card) 55%, var(--card-light) 100%);
    box-shadow: 0 14px 30px rgba(0,0,0,0.6);
    position: relative;
    color: var(--text-light);
    overflow: hidden;
  }
  /* Front */
  .card-front .shop-title {
    position: absolute;
    top: 140px;
    width: 100%;
    text-align: center;
    font-family: "Roboto", sans-serif;
    font-weight: 900;
    font-size: 40px;
    color: var(--emboss);
    text-shadow: 0 1px 0 rgba(255,255,255,0.12), 0 -1px 1px rgba(0,0,0,0.7);
  }
  .card-front .services {
    position: absolute;
    bottom: 44px;
    width: 100%;
    text-align: center;
    font-size: 15px;
    letter-spacing: 0.5px;
  }
  .services .divider { color: var(--accent-blue); margin: 0 6px; }
  /* Back */
  .card-back .shop-title {
    position: absolute;
    left: 30px;
    top: 156px;
    width: 290px;
    white-space: nowrap;
    font-family: "Roboto", sans-serif;
    font-weight: 700;
    font-size: 28px;
    color: var(--brand-blue);
  }
  .card-back .rule {
    position: absolute;
    left: 338px;
    top: 90px;
    width: 2px;
    height: 185px;
    background: var(--text-light);
  }
  .contact {
    position: absolute;
    left: 362px;
    top: 88px;
    width: 250px;
  }
  .contact .name {
    font-size: 24px;
    font-weight: 500;
    letter-spacing: 2.5px;
    color: var(--brand-blue);
    text-transform: uppercase;
    line-height: 1.1;
    white-space: nowrap;
  }
  .contact .role { font-size: 15px; margin-bottom: 14px; }
  .contact .address { font-size: 15px; line-height: 1.45; margin-bottom: 6px; }
  .contact .line {
    display: flex;
    align-items: center;
    gap: 8px;
    font-size: 15px;
    line-height: 1.6;
    white-space: nowrap;
  }
  .contact .line svg { width: 11px; height: 11px; flex: none; }
</style>
</head>
<body>
  <section class="card card-front">
    <h1 class="shop-title">Lantern Healing Shop</h1>
    <p class="services">Reiki Healing<span class="divider">|</span>Tarot<span class="divider">|</span>Oils<span class="divider">|</span>Rituals Of Change</p>
  </section>

  <section class="card card-back">
    <h2 class="shop-title">Lantern Healing Shop</h2>
    <div class="rule"></div>
    <div class="contact">
      <p class="name">Tobin Varley</p>
      <p class="role">Director</p>
      <p class="address">52b Harlow Lane,<br>Ashford, NZ, 8042</p>
      <p class="line">
        <svg viewBox="0 0 12 12"><path d="M2.5 1 L4.5 1 L5.2 3.4 L4 4.4 Q5 6.8 7.6 8 L8.6 6.8 L11 7.5 L11 9.5 Q10.5 11 9 11 Q1 10 1 2.8 Q1 1.2 2.5 1 Z" fill="#3276b5"/></svg>
        (555) 214-7309
      </p>
      <p class="line">
        <svg viewBox="0 0 12 12"><rect x="0.8" y="2.2" width="10.4" height="7.6" fill="none" stroke="#3276b5" stroke-width="1.2"/><path d="M1 2.6 L6 6.6 L11 2.6" fill="none" stroke="#3276b5" stroke-width="1.2"/></svg>
        info@lanternhealingshop.com
      </p>
      <p class="line">
        <svg viewBox="0 0 12 12"><circle cx="6" cy="6" r="5" fill="none" stroke="#3276b5" stroke-width="1.1"/><ellipse cx="6" cy="6" rx="2.2" ry="5" fill="none" stroke="#3276b5" stroke-width="1"/><path d="M1 6 H11 M2 3.5 H10 M2 8.5 H10" stroke="#3276b5" stroke-width="0.9"/></svg>
        www.lanternhealingshop.com
      </p>
    </div>
  </section>
</body>
</html>
```